New Business Card Design for Manufacturing

We are an engineering/manufacturing company that offers Advanced machining/assembly/engineering services, as well as innovative products for the heavy duty engine cooling markets.

We are looking to get a new business card designed that is clean and modern looking, but still fits the wide range of technical/skilled work we do.

- We hope to use this design as the base for other design work in new Presentations, web, and print work.

Industry/Entity Type

Engineering

Contact Information for Business Card

Our preferred color of blue is (RGB) 22/71/159 but can vary slightly from that color. Our content will be our Logo and full company name (Vantrell Forge Works, Inc.), company address, name, job title, phone number with extension, cell number, fax number, website, and email address on the cards.
We'd like the full company name next to the logo, but we are open to other interpretations of that layout.
Preferably, we would like the back side to be clean with just our logo, and the front to contain all of the contact information.

Colors
2f74b4
0355a3
85abd2

Requirements
Must have
• - Logo, company name, needed content - We are open to interpretation beyond that.
• - Standard size business card.
• - Horizontal orientation.
• - Enough space for lengthy names / job titles (for example, a job title could read "Directory of Human Resources" or "V.P. of Governmental Affairs"). We need this to look clean, whether the title be short (CEO) or long (as described above).

```html
<!DOCTYPE html>
<html lang="en">
<head>
<meta charset="utf-8">
<title>Vantrell Forge Works — Business Cards</title>
<link href="https://fonts.googleapis.com/css2?family=Open+Sans:wght@400;600;700&display=swap" rel="stylesheet">
<style>
  :root {
    --page-bg: #e9e7e4;
    --card-bg: #1c1c1d;
    --card-edge: #262628;
    --brand-blue: #2466c4;
    --text-light: #f2f2f2;
    --text-muted: #bfc3c9;
  }
  * { margin: 0; padding: 0; box-sizing: border-box; }
  html, body {
    width: 1200px; height: 715px; overflow: hidden;
    background: var(--page-bg);
    font-family: "Open Sans", Arial, sans-serif;
  }
  .stage {
    position: relative; width: 1200px; height: 715px;
    display: flex; align-items: center; justify-content: center; gap: 50px;
  }
  .card {
    position: relative; width: 525px; height: 300px;
    background: var(--card-bg);
    border: 1px solid var(--card-edge);
    border-radius: 6px;
    color: var(--text-light);
  }
  .brand {
    display: flex; align-items: flex-start; gap: 10px;
  }
  .brand-mark {
    width: 14px; height: 14px; margin-top: 4px;
    background: var(--brand-blue);
    flex: none;
  }
  .brand-name {
    font-weight: 700; color: var(--brand-blue);
    text-transform: uppercase; line-height: 1.05; letter-spacing: 0.5px;
  }
  .brand-tagline {
    margin-top: 8px; font-size: 9px; font-weight: 600;
    letter-spacing: 1px; color: var(--text-muted); text-transform: uppercase;
  }

  /* back side */
  .card-back .brand { position: absolute; left: 120px; top: 92px; }
  .card-back .brand-name { font-size: 26px; }
  .card-back .website {
    position: absolute; left: 0; right: 0; bottom: 46px; text-align: center;
    font-size: 13px; letter-spacing: 1.5px; color: var(--text-light);
  }
  .website .accent { color: var(--brand-blue); }

  /* front side */
  .card-front .brand { position: absolute; left: 34px; top: 104px; width: 200px; }
  .card-front .brand-name { font-size: 17px; }
  .divider {
    position: absolute; left: 258px; top: 48px; width: 1.5px; height: 204px;
    background: var(--brand-blue);
  }
  .contact { position: absolute; left: 282px; top: 52px; right: 20px; }
  .person-name {
    font-size: 17px; font-weight: 600; color: var(--brand-blue);
    letter-spacing: 1px; text-transform: uppercase;
  }
  .person-title { font-size: 12.5px; margin-top: 2px; }
  .address { font-size: 11.5px; line-height: 1.45; margin-top: 10px; }
  .contact-list { list-style: none; margin-top: 10px; }
  .contact-list li {
    display: flex; align-items: center; gap: 9px;
    font-size: 11.5px; line-height: 1.55;
  }
  .contact-list svg { width: 10px; height: 10px; flex: none; fill: var(--brand-blue); }
</style>
</head>
<body>
<main class="stage">

  <section class="card card-back" aria-label="Card back">
    <div class="brand">
      <span class="brand-mark"></span>
      <div>
        <div class="brand-name">Vantrell<br>Forge Works, Inc.</div>
        <div class="brand-tagline">Shaping What's Next</div>
      </div>
    </div>
    <p class="website">www.<span class="accent">vantrellforge</span>.com</p>
  </section>

  <section class="card card-front" aria-label="Card front">
    <div class="brand">
      <span class="brand-mark"></span>
      <div>
        <div class="brand-name">Vantrell<br>Forge Works, Inc.</div>
        <div class="brand-tagline">Shaping What's Next</div>
      </div>
    </div>
    <div class="divider"></div>
    <div class="contact">
      <p class="person-name">Daren Holloway</p>
      <p class="person-title">V.P. of Governmental Affairs</p>
      <p class="address">418 Ironside Avenue,<br>Unit 12/B, Marrowfield</p>
      <ul class="contact-list">
        <li><svg viewBox="0 0 10 10"><path d="M2 0.5l2 2-1 1.2c.6 1.3 1.6 2.3 2.8 2.8L7 5.5l2 2-1.3 1.8C4 9 1 6 .7 2.2z"/></svg>+1 555 204 ext 12</li>
        <li><svg viewBox="0 0 10 10"><rect x="2.5" y="0" width="5" height="10" rx="1"/></svg>+1 555 204 7719</li>
        <li><svg viewBox="0 0 10 10"><rect x="0" y="3" width="10" height="5" rx="1"/><rect x="2.5" y="0.5" width="5" height="2.5"/></svg>+1 555 204 7720</li>
        <li><svg viewBox="0 0 10 10"><path d="M0 2h10v6H0z M0 2l5 3.5L10 2" /></svg>info@vantrellforge.com</li>
        <li><svg viewBox="0 0 10 10"><circle cx="5" cy="5" r="5"/></svg>www.vantrellforge.com</li>
      </ul>
    </div>
  </section>

</main>
</body>
</html>
```